Business Card Design for Marketing Firm

Looking for business card design for higher end marketing firm. Clean but impressionable/trendy. We are a marketing firm that represents manufacturers in the foodservice equipment and supply industry. Our customers are end users such has hotels, restaurants, country clubs, convention centers and casinos as well as distributors of restaurants supplies and equipment, and manufacturers of foodservice equipment and supplies.
Target Market(s)
Hotels, Restaurants, Supply & Equipment Distributors, Foodservice Manufacturers
Industry/Entity Type
Foodservice/Hospitality
Contact Information for Business Card
Name, Title, Contact Number, Email, Website, Social Media, Address
Requirements
Must have
- Clean & Simple but Serious and Impressionable

```html
<!DOCTYPE html>
<html lang="en">
<head>
<meta charset="utf-8">
<title>Meridian Hospitality Reps – Business Card</title>
<link rel="stylesheet" href="https://fonts.googleapis.com/css2?family=Lexend:wght@400;500;600&display=swap">
<style>
  :root {
    --page: #ffffff;
    --card: #ebebeb;
    --navy: #262a78;
    --ink: #232323;
  }
  * { margin: 0; padding: 0; box-sizing: border-box; }
  html, body {
    width: 1200px; height: 1200px; overflow: hidden;
    background: var(--page);
    font-family: "Lexend", sans-serif;
  }
  .canvas { position: relative; width: 1200px; height: 1200px; }
  .card {
    position: absolute; width: 657px; height: 401px;
    background: var(--card); overflow: hidden;
  }
  .card--front { left: 274px; top: 181px; }
  .card--back { left: 277px; top: 625px; }

  .brand {
    position: absolute; left: 0; right: 0; top: 150px;
    display: flex; flex-direction: column; align-items: center; gap: 18px;
  }
  .brand__dot { width: 40px; height: 40px; border-radius: 50%; background: var(--navy); }
  .brand__name {
    color: var(--navy); font-weight: 500; font-size: 22px;
    letter-spacing: 0.06em; text-transform: uppercase;
  }

  .holder { position: absolute; left: 36px; top: 36px; }
  .holder__name { color: var(--navy); font-weight: 600; font-size: 21px; line-height: 1.2; }
  .holder__title { color: var(--ink); font-weight: 400; font-size: 18px; line-height: 1.3; }

  .contacts { position: absolute; left: 37px; top: 167px; list-style: none; }
  .contacts__item {
    display: flex; align-items: center; gap: 10px; height: 26px;
    color: var(--ink); font-weight: 500; font-size: 16px;
  }
  .contacts__icon { width: 18px; height: 18px; flex: none; }
  .contacts__icon--social { border: 2px solid var(--navy); border-radius: 50%; }

  .address {
    position: absolute; left: 36px; top: 303px;
    color: var(--ink); font-size: 15px; line-height: 20px; font-weight: 400;
  }
  .website {
    position: absolute; left: 36px; top: 350px;
    color: var(--ink); font-size: 15px; font-weight: 600;
  }
  .accent-disc {
    position: absolute; left: 400px; top: 200px;
    width: 320px; height: 320px; border-radius: 50%; background: var(--navy);
  }
</style>
</head>
<body>
<main class="canvas">
  <section class="card card--front">
    <div class="brand">
      <span class="brand__dot"></span>
      <span class="brand__name">Meridian Hospitality Reps</span>
    </div>
  </section>

  <section class="card card--back">
    <div class="holder">
      <h1 class="holder__name">Corwin Ashby</h1>
      <p class="holder__title">Chief Operation Marketing</p>
    </div>

    <ul class="contacts">
      <li class="contacts__item">
        <svg class="contacts__icon" viewBox="0 0 24 24" aria-hidden="true">
          <path fill="#262a78" d="M6.6 10.8a15.1 15.1 0 0 0 6.6 6.6l2.2-2.2a1 1 0 0 1 1-.25 11.4 11.4 0 0 0 3.6.57 1 1 0 0 1 1 1V20a1 1 0 0 1-1 1A17 17 0 0 1 3 4a1 1 0 0 1 1-1h3.5a1 1 0 0 1 1 1c0 1.25.2 2.45.57 3.6a1 1 0 0 1-.25 1z"/>
        </svg>
        <span>+00 00 0000 0000</span>
      </li>
      <li class="contacts__item">
        <svg class="contacts__icon" viewBox="0 0 24 24" aria-hidden="true">
          <rect x="2" y="5" width="20" height="14" fill="#262a78"/>
          <path d="M2 5l10 8 10-8M2 19l7-7M22 19l-7-7" stroke="#ebebeb" stroke-width="1.4" fill="none"/>
        </svg>
        <span>corwin.ashby@meridianreps.com</span>
      </li>
      <li class="contacts__item">
        <span class="contacts__icon contacts__icon--social"></span>
        <span>@meridianreps</span>
      </li>
    </ul>

    <p class="address">480 Harbor Lane Suite 210 Lakeside,<br>CA 90210 United States.</p>
    <p class="website">meridianreps.com</p>

    <div class="accent-disc"></div>
  </section>
</main>
</body>
</html>
```